Moldran Foods needs a new label for canned pineapple

We want a very tasty (in terms of making your mouth water) and clean design (less is more) for our canned pineapple under the new logo of Moldran Leafline division

Target Market(s)

The company’s mission is to bring quality food to target audiences of any social status (you receive a bit more than what you spend). Our core values are: reliability, loyalty and commitment to development.
The product is sold to mainstream and lower Mainstream customers.

Requirements
Must have
• The design should take into consideration the visibility on the shelf among competitor products (brief file) and that the product is a MAINSTREAM product.
We want a very tasty (in terms of making your mouth water) and clean design (less is more). The design should be easily modifiable for other canned fruits or vegetables.
The package must display on the front the following elements listed in the order of their should have noticeability:
• Moldran Leaf logo
• Pineapple picture
• Product name
Designers should take into account that the shelfs for displaying the products in the shops may have an elevation of up to 3 cm that can overlap the product label.

Guidelines
• We would like the packaging to be as simple as possible (or at least not to sabotage the Moldran name ), as our strategy depends on the agressive communication of the Moldran logo.
• We would also like to communicate through suggestive and optimal colours as to be easily spotted on the shelf.
• As we have quite a minimal communication budget we need basically for the packaging to do a lot of the communication job itself
• FMCG is a highly visual industry so we have to include pictures of the products on the packages (even more than others do, as we are focused on health and quality - we want people to have that feeling of fresh products even though we are selling canned ones)
Should not have
• but the minimum amount of text on the front.

```html
<!DOCTYPE html>
<html lang="ro">
<head>
<meta charset="utf-8">
<title>Moldran Leafline – Ananas felii</title>
<link rel="stylesheet" href="https://fonts.googleapis.com/css2?family=Josefin+Sans:wght@700&family=Open+Sans:wght@400;600&display=swap">
<style>
  :root {
    --backdrop: #e2e2e2;
    --label-yellow: #ffff0a;
    --slice-white: #ffffff;
    --slice-core: #fbf532;
    --brand-green: #1a8c3c;
    --sub-green: #2f9a4c;
    --ink: #3a3a2a;
  }
  * { margin: 0; padding: 0; box-sizing: border-box; }
  html, body {
    width: 1200px; height: 900px; overflow: hidden;
    background: var(--backdrop);
  }
  .canvas { position: relative; width: 1200px; height: 900px; }
  .label {
    position: absolute; left: 453px; top: 272px;
    width: 324px; height: 388px;
    background: var(--label-yellow);
  }
  .brand {
    position: absolute; left: 0; right: 0; top: 52px;
    display: flex; align-items: center; justify-content: center; gap: 8px;
    font-family: "Open Sans", sans-serif; font-weight: 600;
    font-size: 19px; color: var(--brand-green);
  }
  .brand-dot {
    width: 14px; height: 14px; border-radius: 50%;
    background: var(--brand-green);
  }
  .slice {
    position: absolute; left: 44px; top: 118px;
    width: 244px; height: 244px;
  }
  .product-name {
    position: absolute; left: 58px; top: 218px;
    font-family: "Josefin Sans", sans-serif; font-weight: 700;
    font-size: 35px; letter-spacing: 0.5px; line-height: 1;
    color: var(--brand-green); white-space: nowrap;
  }
  .product-sub {
    position: absolute; left: 57px; top: 250px;
    font-family: "Open Sans", sans-serif; font-weight: 600;
    font-size: 12px; color: var(--sub-green); white-space: nowrap;
  }
  .net-weight {
    position: absolute; left: 262px; top: 308px; width: 62px;
    font-family: "Open Sans", sans-serif; font-size: 12px;
    line-height: 1.25; color: var(--ink); text-align: center;
  }
</style>
</head>
<body>
<main class="canvas">
  <section class="label">
    <div class="brand"><span class="brand-dot"></span><span class="brand-name">Moldran Leafline</span></div>
    <svg class="slice" viewBox="0 0 244 244" aria-hidden="true">
      <defs>
        <radialGradient id="core-glow" cx="40%" cy="45%" r="60%">
          <stop offset="0" stop-color="#fffb8a"/>
          <stop offset="1" stop-color="var(--slice-core)"/>
        </radialGradient>
      </defs>
      <circle cx="122" cy="122" r="122" fill="var(--slice-white)"/>
      <circle cx="122" cy="122" r="62" fill="url(#core-glow)"/>
    </svg>
    <h1 class="product-name">ANANAS FELII</h1>
    <p class="product-sub">in suc indulcit</p>
    <p class="net-weight">298 g ℮<br>175g<br>(uscat)</p>
  </section>
</main>
</body>
</html>
```